Wedding Ceremony Equipment Hire Business Card

I need a business card design for a new business I created called Vowline Rentals. We hire out Wedding Ceremony equipment and decorations mainly for beach and garden wedding ceremonies that include delivery, set up and dismantle. We do offer DIY Chair Hire as well.
I'd like to have a similar design and colours to our website:
www.vowlinerentals.com.au
If possible would like the front to incorporate our information and logo and the back to have two faded example pictures of our wedding ceremonies.
I have attached two photos and our logo. Please let me know if you need a better pic of our logo though.

Target Market(s)

Newly engaged couples, aged 25 and upwards

Industry/Entity Type

Wedding

Contact Information for Business Card

Vowline Rentals
Mira Holt
0412 908 146
hello@vowlinerentals.com.au
www.vowlinesocial.com/VowlineRentals

```html
<!DOCTYPE html>
<html lang="en">
<head>
<meta charset="utf-8">
<title>Vowline Rentals – Business Card</title>
<link href="https://fonts.googleapis.com/css2?family=Cormorant+Garamond:ital,wght@0,500;0,600;1,500&family=Pinyon+Script&display=swap" rel="stylesheet">
<style>
  :root {
    --page: #e6e6e3;
    --card-dark: #2a2a2c;
    --mint: #a8cfc3;
    --mint-light: #c2e0d6;
    --ink: #1f2324;
    --white: #f4f4f2;
    --photo-cool: #a9b7bd;
    --photo-warm: #b9ae9c;
    --photo-sage: #9eab92;
    --shadow: rgba(0, 0, 0, 0.28);
  }
  * { box-sizing: border-box; margin: 0; padding: 0; }
  html, body { width: 1200px; height: 900px; overflow: hidden; }
  body {
    background: var(--page);
    display: flex;
    align-items: center;
    justify-content: center;
    gap: 60px;
  }
  .card {
    position: relative;
    width: 520px;
    height: 325px;
    overflow: hidden;
    box-shadow: 0 6px 18px var(--shadow);
  }
  .card--front { background: var(--card-dark); }
  .card--back { background: var(--white); }

  .brand-band {
    position: absolute;
    left: 0; top: 0;
    width: 100%;
    background: linear-gradient(100deg, var(--mint) 0%, var(--mint-light) 45%, var(--mint) 100%);
  }
  .card--front .brand-band { height: 82px; }
  .card--back .brand-band { height: 86px; }

  .brand-name {
    position: absolute;
    font-family: "Cormorant Garamond", serif;
    font-weight: 600;
    font-size: 28px;
    line-height: 1;
    color: var(--ink);
    letter-spacing: 0.4px;
    white-space: nowrap;
  }
  .card--front .brand-name { left: 22px; top: 27px; }
  .card--back .brand-name { left: 50%; top: 29px; transform: translateX(-38%); }

  .holder-name {
    position: absolute;
    right: 28px;
    top: 132px;
    font-family: "Pinyon Script", cursive;
    font-size: 38px;
    line-height: 1;
    color: var(--white);
    white-space: nowrap;
  }

  .contact-list {
    position: absolute;
    left: 20px;
    bottom: 20px;
    list-style: none;
  }
  .contact-list li {
    display: flex;
    align-items: center;
    gap: 12px;
    height: 22px;
    font-family: "Cormorant Garamond", serif;
    font-style: italic;
    font-weight: 500;
    font-size: 15px;
    color: var(--white);
    white-space: nowrap;
  }
  .contact-icon { width: 12px; height: 12px; flex: none; }

  .photo-pair {
    position: absolute;
    left: 0; top: 90px;
    width: 100%;
    height: 235px;
    display: flex;
    gap: 4px;
  }
  .photo { flex: 1; }
  .photo--beach {
    background: linear-gradient(180deg, var(--photo-cool) 0%, var(--photo-warm) 100%);
  }
  .photo--garden {
    background: linear-gradient(180deg, var(--photo-cool) 0%, var(--photo-sage) 100%);
  }
</style>
</head>
<body>

  <section class="card card--front" aria-label="Business card front">
    <div class="brand-band" role="img" aria-label="Mint band with soft floral damask pattern"></div>
    <div class="brand-name">Vowline Rentals</div>
    <div class="holder-name">Mira Holt</div>
    <ul class="contact-list">
      <li>
        <svg class="contact-icon" viewBox="0 0 12 12" aria-hidden="true">
          <rect x="3" y="0.5" width="6" height="11" rx="1" fill="none" stroke="#f4f4f2" stroke-width="1.2"/>
          <circle cx="6" cy="9.5" r="0.7" fill="#f4f4f2"/>
        </svg>
        0412 908 146
      </li>
      <li>
        <svg class="contact-icon" viewBox="0 0 12 12" aria-hidden="true">
          <circle cx="6" cy="6" r="5.4" fill="none" stroke="#f4f4f2" stroke-width="1.2"/>
          <circle cx="6" cy="6" r="2" fill="none" stroke="#f4f4f2" stroke-width="1.2"/>
        </svg>
        hello@vowlinerentals.com.au
      </li>
      <li>
        <svg class="contact-icon" viewBox="0 0 12 12" aria-hidden="true">
          <rect x="0.6" y="2.2" width="10.8" height="7.6" fill="none" stroke="#f4f4f2" stroke-width="1.2"/>
          <path d="M0.8 2.6 L6 6.6 L11.2 2.6" fill="none" stroke="#f4f4f2" stroke-width="1.2"/>
        </svg>
        www.vowlinerentals.com.au
      </li>
      <li>
        <svg class="contact-icon" viewBox="0 0 12 12" aria-hidden="true">
          <rect x="0.5" y="0.5" width="11" height="11" rx="1.5" fill="#f4f4f2"/>
        </svg>
        www.vowlinesocial.com/VowlineRentals
      </li>
    </ul>
  </section>

  <section class="card card--back" aria-label="Business card back">
    <div class="brand-band" role="img" aria-label="Mint band with soft floral damask pattern"></div>
    <div class="brand-name">Vowline Rentals</div>
    <div class="photo-pair">
      <div class="photo photo--beach" role="img" aria-label="Faded photo of a beach wedding ceremony set-up"></div>
      <div class="photo photo--garden" role="img" aria-label="Faded photo of a garden wedding ceremony set-up"></div>
    </div>
  </section>

</body>
</html>
```